Create a new business card

I’m looking to update my business card to make it match the rest of my brand. I will include my current website as well as what my vehicle designs look like, etc..
What my business currently services
Weekly maintenance pool openings / closings
Equipment repair, including pumps, heaters, salt systems, filters, etc.
We install automatic covers and maintain them as well as provide preventative maintenance

I would like to include my name.
Dorian Pelkin.
My title
Owner
My email
Dorian@tidewellnx.com
4015827160
Www.tidewellnx.com

```html
<!DOCTYPE html>
<html lang="en">
<head>
<meta charset="utf-8">
<title>Tidewell Pool Service — Business Card</title>
<link href="https://fonts.googleapis.com/css2?family=Oswald:wght@300;400;600&display=swap" rel="stylesheet">
<style>
  :root {
    --navy: #1e2c63;
    --sky: #2aa7e0;
    --orange: #e8632a;
    --white: #ffffff;
    --stage: #2a2a2c;
  }
  * { box-sizing: border-box; margin: 0; padding: 0; }
  html, body { width: 1200px; height: 1122px; overflow: hidden; background: var(--stage); }
  .canvas { position: relative; width: 1200px; height: 1122px; }
  .card {
    position: absolute; left: 150px; width: 900px; height: 514px;
    border-radius: 34px; overflow: hidden;
    font-family: "Oswald", sans-serif;
  }
  .card--back { top: 30px; background: var(--navy); }
  .card--front { top: 578px; background: var(--white); }

  .brand {
    position: absolute; display: flex; align-items: center; gap: 16px;
  }
  .brand__dot { width: 46px; height: 46px; border-radius: 50%; background: var(--sky); flex: none; }
  .brand__name {
    font-weight: 600; font-size: 38px; line-height: 1.05; text-transform: uppercase; letter-spacing: 1px;
  }
  .card--back .brand { left: 50px; top: 205px; }
  .card--back .brand__name { color: var(--white); }
  .card--front .brand { left: 50px; top: 205px; }
  .card--front .brand__name { color: var(--navy); }

  .divider {
    position: absolute; left: 418px; top: 70px; width: 3px; height: 374px; background: var(--orange);
  }
  .services {
    position: absolute; left: 450px; top: 58px; list-style: none;
  }
  .services li {
    display: flex; align-items: center; gap: 12px;
    color: var(--white); font-weight: 400; font-size: 21px; line-height: 36px;
    text-transform: uppercase; letter-spacing: 1px;
  }
  .services svg { width: 20px; height: 20px; flex: none; }

  .front-shape { position: absolute; inset: 0; }
  .contact {
    position: absolute; right: 70px; top: 150px; text-align: right;
  }
  .contact__name {
    color: var(--sky); font-weight: 600; font-size: 56px; line-height: 1; text-transform: uppercase; letter-spacing: 1px;
  }
  .contact__title {
    color: var(--orange); font-weight: 400; font-size: 32px; line-height: 1.2; text-transform: uppercase; margin-bottom: 14px;
  }
  .contact__row {
    display: flex; justify-content: flex-end; align-items: center; gap: 16px;
    color: var(--white); font-weight: 300; font-size: 30px; line-height: 46px; text-transform: uppercase;
  }
  .contact__row--phone { font-weight: 400; font-size: 34px; }
  .contact__row svg { width: 26px; height: 26px; flex: none; }
</style>
</head>
<body>
<div class="canvas">

  <section class="card card--back">
    <div class="brand">
      <span class="brand__dot"></span>
      <span class="brand__name">Tidewell<br>Pool Service</span>
    </div>
    <div class="divider"></div>
    <ul class="services">
      <li><svg viewBox="0 0 20 20"><circle cx="10" cy="10" r="10" fill="#2aa7e0"/><path d="M5.5 10.5l3 3 6-6" stroke="#fff" stroke-width="2.4" fill="none"/></svg>Weekly Pool Maintenance</li>
      <li><svg viewBox="0 0 20 20"><circle cx="10" cy="10" r="10" fill="#2aa7e0"/><path d="M5.5 10.5l3 3 6-6" stroke="#fff" stroke-width="2.4" fill="none"/></svg>Pool Opening &amp; Closing</li>
      <li><svg viewBox="0 0 20 20"><circle cx="10" cy="10" r="10" fill="#2aa7e0"/><path d="M5.5 10.5l3 3 6-6" stroke="#fff" stroke-width="2.4" fill="none"/></svg>Equipment Servicing</li>
      <li><svg viewBox="0 0 20 20"><circle cx="10" cy="10" r="10" fill="#2aa7e0"/><path d="M5.5 10.5l3 3 6-6" stroke="#fff" stroke-width="2.4" fill="none"/></svg>Equipment Installation</li>
      <li><svg viewBox="0 0 20 20"><circle cx="10" cy="10" r="10" fill="#2aa7e0"/><path d="M5.5 10.5l3 3 6-6" stroke="#fff" stroke-width="2.4" fill="none"/></svg>Structural Pool Repair</li>
      <li><svg viewBox="0 0 20 20"><circle cx="10" cy="10" r="10" fill="#2aa7e0"/><path d="M5.5 10.5l3 3 6-6" stroke="#fff" stroke-width="2.4" fill="none"/></svg>Plumbing Updates &amp; Upgrades</li>
      <li><svg viewBox="0 0 20 20"><circle cx="10" cy="10" r="10" fill="#2aa7e0"/><path d="M5.5 10.5l3 3 6-6" stroke="#fff" stroke-width="2.4" fill="none"/></svg>Coping Replacement &amp; Removal</li>
      <li><svg viewBox="0 0 20 20"><circle cx="10" cy="10" r="10" fill="#2aa7e0"/><path d="M5.5 10.5l3 3 6-6" stroke="#fff" stroke-width="2.4" fill="none"/></svg>Tile Replacement &amp; Removal</li>
      <li><svg viewBox="0 0 20 20"><circle cx="10" cy="10" r="10" fill="#2aa7e0"/><path d="M5.5 10.5l3 3 6-6" stroke="#fff" stroke-width="2.4" fill="none"/></svg>Interior Resurfacing/Replastering</li>
      <li><svg viewBox="0 0 20 20"><circle cx="10" cy="10" r="10" fill="#2aa7e0"/><path d="M5.5 10.5l3 3 6-6" stroke="#fff" stroke-width="2.4" fill="none"/></svg>Filter System Equipment Upgrades</li>
      <li><svg viewBox="0 0 20 20"><circle cx="10" cy="10" r="10" fill="#2aa7e0"/><path d="M5.5 10.5l3 3 6-6" stroke="#fff" stroke-width="2.4" fill="none"/></svg>Decking Removal &amp; Renovation</li>
    </ul>
  </section>

  <section class="card card--front">
    <svg class="front-shape" viewBox="0 0 900 514" width="900" height="514">
      <defs>
        <path id="wave" d="M600 0 C470 0 450 120 430 250 C410 390 350 514 250 514 L960 514 L960 0 Z"/>
      </defs>
      <use href="#wave" fill="#e8632a" transform="translate(-34 0)"/>
      <use href="#wave" fill="#ffffff" transform="translate(-22 0)"/>
      <use href="#wave" fill="#2aa7e0" transform="translate(-17 0)"/>
      <use href="#wave" fill="#ffffff" transform="translate(-8 0)"/>
      <use href="#wave" fill="#1e2c63"/>
    </svg>

    <div class="brand">
      <span class="brand__dot"></span>
      <span class="brand__name">Tidewell<br>Pool Service</span>
    </div>

    <div class="contact">
      <h1 class="contact__name">Dorian Pelkin</h1>
      <p class="contact__title">Owner</p>
      <p class="contact__row contact__row--phone">(401) 582-7160
        <svg viewBox="0 0 24 24"><path d="M6.6 2.5l3 3.2-1.8 2.4c1.2 2.7 3.3 4.8 6 6l2.4-1.8 3.3 3-1.6 3.2C11 18.4 5.6 13 4 5.1z" fill="none" stroke="#2aa7e0" stroke-width="2"/></svg>
      </p>
      <p class="contact__row">Dorian@tidewellnx.com
        <svg viewBox="0 0 24 24"><rect x="2" y="5" width="20" height="14" fill="#2aa7e0"/><path d="M2 5l10 8 10-8" stroke="#1e2c63" stroke-width="1.6" fill="none"/></svg>
      </p>
      <p class="contact__row">tidewellnx.com
        <svg viewBox="0 0 24 24"><circle cx="12" cy="12" r="10" fill="#2aa7e0"/><ellipse cx="12" cy="12" rx="4" ry="10" fill="none" stroke="#1e2c63" stroke-width="1.4"/><path d="M2 12h20" stroke="#1e2c63" stroke-width="1.4"/></svg>
      </p>
    </div>
  </section>

</div>
</body>
</html>
```